Veranix - Solution provider in business consulting

Veranix is a swiss based company providing solutions for developing markets. The business covers various fields of business consulting, such as supply chain, product costs, quality management and manufacturing management. The Business operates in a efficient, straight and solution oriented manner.
The final design should communicate these characteristics. Asian people as well as as western people shall identify the qualities of the company at first sight.
The customer needs business cards with a simple view but an recognizable design, printed in high quality. Engraved elements such as the globe or simple words are possible.
Available colors are: (RAL)
102/102/102
51/102/102
153/204/153
255/102/51
Font: Calibri

```html
<!DOCTYPE html>
<html lang="en">
<head>
<meta charset="utf-8">
<title>Veranix business card</title>
<link rel="stylesheet" href="https://fonts.googleapis.com/css2?family=Carlito:wght@400;700&display=swap">
<style>
  :root {
    --backdrop: #efeeeb;
    --card-white: #f7f7f5;
    --emboss: #e2e2de;
    --card-grey: #666666;
    --ink-white: #ffffff;
    --mark-grey: #666666;
  }
  html, body {
    margin: 0;
    padding: 0;
    width: 1200px;
    height: 795px;
    overflow: hidden;
    background: var(--backdrop);
    font-family: "Carlito", "Calibri", sans-serif;
  }
  .canvas {
    position: relative;
    width: 1200px;
    height: 795px;
  }
  .card {
    position: absolute;
    top: 235px;
    width: 520px;
    height: 336px;
    box-sizing: border-box;
    box-shadow: 0 2px 6px rgba(0,0,0,0.12);
  }
  .card--front {
    left: 50px;
    background: var(--card-white);
  }
  .card--back {
    left: 630px;
    background: var(--card-grey);
    color: var(--ink-white);
  }

  /* front */
  .brand {
    position: absolute;
    left: 0;
    right: 0;
    top: 132px;
    display: flex;
    align-items: center;
    justify-content: center;
    gap: 16px;
  }
  .brand__dot {
    width: 58px;
    height: 58px;
    border-radius: 50%;
    background: var(--mark-grey);
  }
  .brand__name {
    font-size: 62px;
    font-weight: 400;
    color: var(--emboss);
    letter-spacing: 1px;
    line-height: 1;
  }

  /* back */
  .back__dot {
    position: absolute;
    top: 26px;
    right: 34px;
    width: 40px;
    height: 40px;
    border-radius: 50%;
    background: var(--ink-white);
  }
  .person {
    position: absolute;
    left: 34px;
    top: 116px;
  }
  .person__name {
    font-size: 27px;
    line-height: 1.05;
  }
  .person__role {
    font-size: 17px;
    margin-top: 3px;
  }
  .divider {
    position: absolute;
    left: 34px;
    right: 34px;
    top: 176px;
    height: 1.5px;
    background: var(--ink-white);
  }
  .contacts {
    position: absolute;
    left: 34px;
    top: 188px;
    list-style: none;
    margin: 0;
    padding: 0;
    font-size: 17px;
    line-height: 25px;
  }
  .contacts li {
    display: flex;
    align-items: center;
    gap: 10px;
  }
  .contacts svg {
    width: 14px;
    height: 14px;
    flex: none;
  }
  .address {
    position: absolute;
    right: 34px;
    top: 188px;
    text-align: right;
    font-size: 17px;
    line-height: 22px;
    font-style: normal;
  }
</style>
</head>
<body>
<main class="canvas">

  <section class="card card--front" aria-label="Business card front">
    <div class="brand">
      <span class="brand__name">veranix</span>
      <span class="brand__dot"></span>
    </div>
  </section>

  <section class="card card--back" aria-label="Business card back">
    <span class="back__dot"></span>

    <div class="person">
      <div class="person__name">Marco Albrecht</div>
      <div class="person__role">CEO</div>
    </div>

    <div class="divider"></div>

    <ul class="contacts">
      <li>
        <svg viewBox="0 0 14 14" aria-hidden="true"><path d="M3 1 L5.5 1 L6.5 4 L5 5.2 C5.8 7 7 8.2 8.8 9 L10 7.5 L13 8.5 L13 11 C13 12 12 13 11 13 C5.5 13 1 8.5 1 3 C1 2 2 1 3 1 Z" fill="#fff"/></svg>
        <span>+41 71 860 3190</span>
      </li>
      <li>
        <svg viewBox="0 0 14 14" aria-hidden="true"><rect x="3.5" y="0.8" width="7" height="12.4" rx="1.2" fill="none" stroke="#fff" stroke-width="1.4"/><circle cx="7" cy="11" r="0.8" fill="#fff"/></svg>
        <span>+41 79 527 4408</span>
      </li>
      <li>
        <svg viewBox="0 0 14 14" aria-hidden="true"><rect x="0.8" y="2.5" width="12.4" height="9" fill="none" stroke="#fff" stroke-width="1.4"/><path d="M1 3 L7 8 L13 3" fill="none" stroke="#fff" stroke-width="1.4"/></svg>
        <span>marco.albrecht@veranix.ch</span>
      </li>
      <li>
        <svg viewBox="0 0 14 14" aria-hidden="true"><circle cx="7" cy="7" r="6" fill="none" stroke="#fff" stroke-width="1.4"/><path d="M5 4 L10 7 L5 10 Z" fill="#fff"/></svg>
        <span>www.veranix.ch</span>
      </li>
    </ul>

    <address class="address">
      Veranix GmbH<br>
      Lindenweg 18<br>
      9240 Talheim<br>
      Switzerland
    </address>
  </section>

</main>
</body>
</html>
```